Business Card Design

New business card design

Target Market(s)

Residential & Commercial Property Managers

Industry/Entity Type

Plumbing Services

Contact Information for Business Card

Name - Rowan Keddle, title - Director, Phone Number - 0431 286 517, email - rowan@tbk-plumbing.com.au, Company ABN - 73 215 904 386,

Font styles to use
Sans Serif

Colors
0054AA
0677BA
7BADD7
CADEEF
E8F1F8

```html
<!DOCTYPE html>
<html lang="en">
<head>
<meta charset="utf-8">
<title>TBK Plumbing Services – Business Card</title>
<link href="https://fonts.googleapis.com/css2?family=Montserrat:wght@400;500;700&display=swap" rel="stylesheet">
<style>
  :root {
    --stage: #222222;
    --paper: #ffffff;
    --ink: #1d252e;
    --band: #262b33;
    --accent: #2aa7e1;
  }
  html, body {
    margin: 0;
    width: 1200px;
    height: 780px;
    overflow: hidden;
    background: var(--stage);
    font-family: "Montserrat", sans-serif;
  }
  .canvas {
    position: relative;
    width: 1200px;
    height: 780px;
  }
  .card {
    position: absolute;
    top: 240px;
    width: 520px;
    height: 300px;
    background: var(--paper);
    overflow: hidden;
  }
  .card--details { left: 60px; }
  .card--brand { left: 620px; }

  .wave { position: absolute; inset: 0; }

  .identity {
    position: absolute;
    top: 26px;
    left: 0;
    padding-left: 34px;
  }
  .identity__bar {
    position: absolute;
    left: 0;
    top: 2px;
    width: 20px;
    height: 24px;
    background: var(--accent);
  }
  .identity__name {
    margin: 0;
    font-weight: 700;
    font-size: 24px;
    line-height: 28px;
    color: var(--accent);
  }
  .identity__title {
    margin: 2px 0 0;
    font-weight: 400;
    font-size: 13px;
    color: var(--ink);
  }

  .contact {
    position: absolute;
    left: 22px;
    top: 175px;
    margin: 0;
    padding: 0;
    list-style: none;
    color: var(--paper);
    font-size: 12.5px;
    line-height: 18px;
  }
  .contact li {
    display: flex;
    align-items: center;
    gap: 7px;
    margin-bottom: 5px;
  }
  .contact__icon { width: 12px; height: 12px; flex: none; }
  .contact__abn { padding-left: 19px; }

  .brand {
    position: absolute;
    display: flex;
    align-items: center;
    gap: 10px;
    color: var(--ink);
    font-weight: 500;
    white-space: nowrap;
  }
  .brand__dot {
    border-radius: 50%;
    background: var(--accent);
    flex: none;
  }
  .card--details .brand {
    right: 26px;
    top: 120px;
    font-size: 22px;
  }
  .card--details .brand__dot { width: 16px; height: 16px; }
  .card--brand .brand {
    left: 50%;
    top: 50%;
    transform: translate(-50%, -50%);
    font-size: 34px;
  }
  .card--brand .brand__dot { width: 24px; height: 24px; }
</style>
</head>
<body>
<main class="canvas">

  <section class="card card--details" aria-label="Business card, contact side">
    <svg class="wave" viewBox="0 0 520 300" aria-hidden="true">
      <path d="M0,120 C60,112 120,125 180,160 C260,210 320,290 470,300 L0,300 Z" fill="var(--band)"/>
      <path d="M0,120 C60,112 120,125 180,160 C260,210 320,290 470,300" fill="none" stroke="var(--paper)" stroke-width="10"/>
      <path d="M24,112 C80,108 140,120 196,152 C276,200 336,280 520,290" fill="none" stroke="var(--accent)" stroke-width="4"/>
    </svg>

    <div class="identity">
      <span class="identity__bar"></span>
      <h1 class="identity__name">Rowan Keddle</h1>
      <p class="identity__title">Director</p>
    </div>

    <div class="brand">
      <span class="brand__dot"></span>
      <span class="brand__name">tbk plumbing services</span>
    </div>

    <ul class="contact">
      <li class="contact__abn">Company ABN<br>- 73 215 904 386</li>
      <li>
        <svg class="contact__icon" viewBox="0 0 24 24" aria-hidden="true">
          <path d="M6.6 10.8a15 15 0 0 0 6.6 6.6l2.2-2.2a1 1 0 0 1 1-.25 11.4 11.4 0 0 0 3.6.57 1 1 0 0 1 1 1V20a1 1 0 0 1-1 1A17 17 0 0 1 3 4a1 1 0 0 1 1-1h3.5a1 1 0 0 1 1 1c0 1.25.2 2.450.57 3.57a1 1 0 0 1-.25 1z" fill="var(--accent)"/>
        </svg>
        <span>0431 286 517</span>
      </li>
      <li>
        <svg class="contact__icon" viewBox="0 0 24 24" aria-hidden="true">
          <rect x="2" y="5" width="20" height="14" rx="1.5" fill="var(--accent)"/>
          <path d="M3 6l9 7 9-7" fill="none" stroke="var(--band)" stroke-width="1.8"/>
        </svg>
        <span>rowan@tbk-plumbing.com.au</span>
      </li>
    </ul>
  </section>

  <section class="card card--brand" aria-label="Business card, brand side">
    <div class="brand">
      <span class="brand__dot"></span>
      <span class="brand__name">tbk plumbing services</span>
    </div>
  </section>

</main>
</body>
</html>
```